Contemporary Business card for Event Manager

Needed for my startup events company in Melbourne. Events I manage will be based within the fashion industry, sporting events, product launches etc. Not weddings or small dinner parties. Therfore I am after something professional and aimed at high end corporate market; but with the added emphasis on not being too conservative or boring. I am happy with a pop of colour e.g. yellow or copper foil.

Target Market(s)

fashion industry, design industry, high end sporting events e.g. Polo, Grand Prix, corporate clients,

Industry/Entity Type

Fashion

Contact Information for Business Card

side 1
Lucy Brandt (can be upper or lower case, have a feature full stop between first and surname, or at the end of the nameetc) I am open to ideas. I would also be fine with my initials or name as a logo on the front (if this is the case my full name would need to go on the second side of the card.
2nd side:
Mobile: +61 400 817 263
email: lucy.brandt@mailnest.com.au

on one side of the card:
event management | brand activation | Advisory Services

Font styles to use
Serif
Sans Serif

Requirements
Must have
• side 2 must have
• mobile number
• email address
• event management | brand activation | Advisory Services
• ** my full name (Lucy Brandt) must be on the card somewhere)
Nice to have
• 1st side
• I see the card stock being either a dark grey, light grey, natural white or black (all matt colours on unprocessed card). I see the writing being copper foil, or foil white or foil black.
• To give you a feel for me, think: contemporary, minimalist, I love line drawings, concrete, white with grey vein marble, copper, white, grey, black...yes I do like colour....yellow (but pops of colour) ;) I would like the card to look designer but 'on trend' as I deal with a lot of design and fashion clients....styles - think the sophistication and simplicity of Vireaux or urban contemporary.
• some examples of what I like. Although please don't leet this limit you...I really am happy to have something a little more urban or design focused like a line drawing of an object, person too or a photo image too.
• https://www.moodtackle.com/pin/830165427719302846/
• https://www.moodtackle.com/pin/607281935540173268/
• https://www.moodtackle.com/pin/318746205913457092/
• https://www.moodtackle.com/pin/41983627530918476/
• https://www.moodtackle.com/pin/53128940672419087/
• https://www.moodtackle.com/pin/90316284750638152/
• https://www.moodtackle.com/pin/734092618450362918/
• https://www.moodtackle.com/pin/926354081736215407/
• https://www.moodtackle.com/pin/481627093518704356/
Should not have
• should not look commercial or have cartoonish looking logos. However happy with a simple line drawing or logo with initials etc.

```html
<!DOCTYPE html>
<html lang="en">
<head>
<meta charset="utf-8">
<title>Lucy Brandt – Business Card</title>
<link rel="stylesheet" href="https://fonts.googleapis.com/css2?family=Marcellus&family=Quicksand:wght@300;400&display=swap">
<style>
  :root {
    --backdrop: #e4e2df;
    --violet: #7f2591;
    --ink: #0c0b0d;
    --stripe: #f1eef3;
    --name-tint: #efe9f2;
    --type-light: #e9e9ea;
  }
  html, body {
    margin: 0;
    width: 1200px;
    height: 902px;
    overflow: hidden;
    background: var(--backdrop);
  }
  .canvas {
    position: relative;
    width: 1200px;
    height: 902px;
  }
  .card {
    position: absolute;
    left: 290px;
    width: 620px;
    height: 379px;
    border-radius: 4px;
    overflow: hidden;
    box-shadow: 0 6px 18px rgba(0,0,0,.22);
  }
  .card--front { top: 42px; }
  .card--back { top: 481px; }
  .card svg { position: absolute; inset: 0; display: block; }
  .card__name {
    position: absolute;
    left: 0; right: 0;
    top: 164px;
    margin: 0;
    text-align: center;
    font-family: "Marcellus", serif;
    font-weight: 400;
    font-size: 36px;
    letter-spacing: .12em;
    color: var(--name-tint);
  }
  .services {
    position: absolute;
    right: 62px;
    top: 54px;
    margin: 0;
    padding: 0;
    list-style: none;
    text-align: right;
    font-family: "Quicksand", sans-serif;
    font-weight: 300;
    font-size: 18px;
    line-height: 25px;
    color: var(--type-light);
  }
  .accent { color: var(--violet); }
  .contact {
    position: absolute;
    left: 100px;
    bottom: 34px;
    font-family: "Quicksand", sans-serif;
    font-weight: 300;
    font-size: 19px;
    line-height: 27px;
    color: var(--type-light);
  }
  .contact p { margin: 0; }
</style>
</head>
<body>
<main class="canvas">

  <section class="card card--front" aria-label="Card front">
    <svg viewBox="0 0 620 379" width="620" height="379" aria-hidden="true">
      <rect width="620" height="379" fill="var(--violet)"/>
      <polygon points="0,0 122,0 12,379 0,379" fill="var(--ink)"/>
      <line x1="125" y1="-2" x2="15" y2="381" stroke="var(--stripe)" stroke-width="7"/>
      <polygon points="604,0 620,0 620,379 494,379" fill="var(--ink)"/>
      <line x1="601" y1="-2" x2="491" y2="381" stroke="var(--stripe)" stroke-width="7"/>
    </svg>
    <h1 class="card__name">LUCY BRANDT</h1>
  </section>

  <section class="card card--back" aria-label="Card back">
    <svg viewBox="0 0 620 379" width="620" height="379" aria-hidden="true">
      <rect width="620" height="379" fill="var(--ink)"/>
      <polygon points="0,0 172,0 62,379 0,379" fill="var(--violet)"/>
      <line x1="175" y1="-2" x2="65" y2="381" stroke="var(--stripe)" stroke-width="7"/>
      <polygon points="652,0 620,0 620,379 542,379" fill="var(--violet)"/>
      <line x1="649" y1="-2" x2="539" y2="381" stroke="var(--stripe)" stroke-width="7"/>
    </svg>
    <ul class="services">
      <li>event <span class="accent">management</span></li>
      <li>brand <span class="accent">activation</span></li>
      <li>Advisory <span class="accent">Services</span></li>
    </ul>
    <div class="contact">
      <p class="contact__phone">+61 400 817 263</p>
      <p class="contact__email"><span class="accent">lucy.brandt</span>@mailnest.com.au</p>
    </div>
  </section>

</main>
</body>
</html>
```